Hello my name is Colin, I am Starting a business called Lumen Wellness and fitness and am in need of a memorable business card.
It is a personal training studio. I have added the logo that i would like to be on the left center om my business card. i would like room left up the top for a heading sentence such as. "Is your body shocking for all the wrong reasons". there must be room left on the right of the logo below the main heading for 3 sub headings.
then under those 3 headings and logo room for another larger heading eg. "give me a call and learn how to eat chocolate, drink bear and have great sex". in what room is left i would like to be used for my contact details, use I'm Colin Ferrante your fitness expert on the left then on the right Phone, Email and website space in at least 12 Point. Very specific i know :) now onto the back, for the back i would like an eye catching graphic and room for one main headline and 3 bullet points centered just write anything i will choose what to put in them when i pick a winner. Thank you very much for sticking through all of that :) i appreciate you taking the time to read it and hopefully undergo designing me a business card.
I can't wait to see the designs!

Target Market(s)

slightly more towards females although it would probably be best if it was targeted towards both sexes

Industry/Entity Type

Training

Requirements
Nice to have
• I would love to see if anyone could come up with a design that would really make my card stand out and be memorable.
Should not have
• tacky fitness photos of abs and muscles etc.

```html
<!DOCTYPE html>
<html lang="en">
<head>
<meta charset="utf-8">
<title>Lumen Wellness and fitness – Business Card</title>
<link rel="stylesheet" href="https://fonts.googleapis.com/css2?family=Questrial&family=Open+Sans:wght@400&family=PT+Sans:wght@400&display=swap">
<style>
  :root {
    --stage: #ebe8e4;
    --card: #ffffff;
    --brand: #1d4f86;
    --brand-deep: #173f6d;
    --band-end: #0f3460;
    --band-tab: #3a3a3c;
    --ink: #3d3d3d;
    --ink-soft: #555555;
    --label: #222222;
    --figure-top: #1f5490;
    --figure-bottom: #163a66;
  }
  * { margin: 0; padding: 0; box-sizing: border-box; }
  html, body { width: 1200px; height: 788px; overflow: hidden; }
  body {
    position: relative;
    background: var(--stage);
    font-family: "Questrial", "Century Gothic", sans-serif;
    color: var(--ink);
  }
  .view-label {
    position: absolute;
    font-family: "PT Sans", "Myriad Pro", sans-serif;
    font-size: 21px;
    color: var(--label);
    transform: translateX(-50%);
  }
  .card {
    position: absolute;
    width: 525px;
    height: 300px;
    background: var(--card);
    border-radius: 20px;
    box-shadow: 0 4px 14px rgba(0,0,0,0.28);
    overflow: hidden;
  }
  .card--front { left: 337px; top: 74px; }
  .card--back-list { left: 54px; top: 446px; }
  .card--back-logo { left: 621px; top: 441px; }

  .tagline { position: absolute; font-size: 13px; line-height: 16px; color: var(--ink); }

  .brand { position: absolute; color: var(--brand); font-family: "Questrial", sans-serif; font-weight: 400; }
  .brand__name { display: block; letter-spacing: -1px; }
  .brand__sub { display: block; text-align: right; }

  .card--front .tagline { left: 28px; top: 22px; }
  .card--front .brand { left: 26px; top: 92px; width: 230px; }
  .card--front .brand__name { font-size: 72px; line-height: 70px; }
  .card--front .brand__sub { font-size: 17px; line-height: 20px; }

  .promo { position: absolute; left: 28px; top: 226px; font-size: 13px; line-height: 17px; color: var(--ink); }

  .name-band {
    position: absolute; left: 339px; top: 153px; width: 186px; height: 50px;
    background: linear-gradient(90deg, var(--brand) 0%, var(--band-end) 85%);
  }
  .name-band::after {
    content: ""; position: absolute; right: 0; top: 0; width: 27px; height: 100%;
    background: var(--band-tab);
  }
  .name-band__text {
    position: absolute; left: 13px; top: 8px; font-size: 13px; line-height: 17px; color: #fff;
  }
  .contact { position: absolute; left: 351px; top: 215px; list-style: none; font-size: 13px; }
  .contact__item { display: flex; align-items: center; height: 22px; color: var(--ink); }
  .contact__icon { width: 12px; height: 12px; margin-right: 6px; fill: var(--ink-soft); }

  .card--back-list .tagline { left: 42px; top: 20px; }
  .card--back-list .brand { left: 256px; top: 20px; width: 124px; }
  .card--back-list .brand__name { font-size: 36px; line-height: 34px; }
  .card--back-list .brand__sub { font-size: 9.5px; line-height: 12px; }
  .figure-art {
    position: absolute; left: 42px; top: 78px; width: 114px; height: 206px;
    background: linear-gradient(180deg, var(--figure-top), var(--figure-bottom));
    border-radius: 40px 40px 8px 8px;
  }
  .points { position: absolute; left: 257px; top: 117px; list-style: none; font-family: "Open Sans", sans-serif; font-size: 16px; color: #111; }
  .points__item { position: relative; padding-left: 26px; height: 32px; line-height: 22px; }
  .points__item:nth-child(3) { margin-top: 4px; }
  .points__item::before {
    content: ""; position: absolute; left: 0; top: 8px; width: 6px; height: 6px; background: #111;
  }
  .card--back-list .web { position: absolute; left: 256px; top: 253px; font-size: 19px; color: var(--ink); }

  .card--back-logo .tagline { left: 0; right: 0; top: 20px; text-align: center; }
  .card--back-logo .brand { left: 106px; top: 82px; width: 312px; }
  .card--back-logo .brand__name { font-size: 98px; line-height: 94px; text-align: center; }
  .card--back-logo .brand__sub { font-size: 23px; line-height: 28px; }
  .card--back-logo .web {
    position: absolute; left: 0; right: 0; top: 252px; text-align: center;
    font-size: 20px; letter-spacing: 4px; color: var(--ink);
  }
</style>
</head>
<body>
  <span class="view-label" style="left:600px; top:32px;">Front</span>
  <span class="view-label" style="left:323px; top:402px;">Back - 1</span>
  <span class="view-label" style="left:897px; top:402px;">Back - 2</span>

  <section class="card card--front">
    <p class="tagline">Is your body shocking for all<br>the wrong reasons</p>
    <div class="brand">
      <span class="brand__name">Lumen</span>
      <span class="brand__sub">Wellness and fitness</span>
    </div>
    <p class="promo">give me a call and learn how<br>to eat chocolate, drink bear<br>and have great sex</p>
    <div class="name-band">
      <p class="name-band__text">Colin Ferrante<br>Fitness Expert</p>
    </div>
    <ul class="contact">
      <li class="contact__item">
        <svg class="contact__icon" viewBox="0 0 12 12"><path d="M2.5 0.5 L4.5 0.5 L5.2 3.2 L3.8 4.3 C4.5 5.8 6.2 7.5 7.7 8.2 L8.8 6.8 L11.5 7.5 L11.5 9.5 C11.5 10.6 10.6 11.5 9.5 11.5 C4.5 11.2 0.8 7.5 0.5 2.5 C0.5 1.4 1.4 0.5 2.5 0.5 Z"/></svg>
        +12 345 67890
      </li>
      <li class="contact__item">
        <svg class="contact__icon" viewBox="0 0 12 12"><path d="M0.5 4 L6 1 L11.5 4 L11.5 11 L0.5 11 Z M1.5 4.6 L6 7.4 L10.5 4.6 L6 2.1 Z"/></svg>
        info@website.com
      </li>
      <li class="contact__item">
        <svg class="contact__icon" viewBox="0 0 12 12" fill="none"><g fill="none" stroke="#555" stroke-width="1"><circle cx="6" cy="6" r="5.2"/><ellipse cx="6" cy="6" rx="2.3" ry="5.2"/><line x1="0.8" y1="6" x2="11.2" y2="6"/></g></svg>
        www.website.com
      </li>
    </ul>
  </section>

  <section class="card card--back-list">
    <p class="tagline">Is your body shocking for all<br>the wrong reasons</p>
    <div class="brand">
      <span class="brand__name">Lumen</span>
      <span class="brand__sub">Wellness and fitness</span>
    </div>
    <div class="figure-art" role="img" aria-label="Blue silhouettes of a man in a suit and a woman standing side by side"></div>
    <ul class="points">
      <li class="points__item">Lorem Ipsum has been ...</li>
      <li class="points__item">Lorem Ipsum has been ...</li>
      <li class="points__item">Lorem Ipsum has been ...</li>
    </ul>
    <p class="web">www.website.com</p>
  </section>

  <section class="card card--back-logo">
    <p class="tagline">Is your body shocking for all the wrong reasons</p>
    <div class="brand">
      <span class="brand__name">Lumen</span>
      <span class="brand__sub">Wellness and fitness</span>
    </div>
    <p class="web">www.website.com</p>
  </section>
</body>
</html>
```